Business card design for my company.
I would like the card's background colour to be black. You can also see our web site to get an idea of our brand. https://www.tmwhomecrafting.com.au/
- Name
- Email

```html
<!DOCTYPE html>
<html lang="en">
<head>
<meta charset="utf-8">
<title>TMW Home Crafting – Business Card</title>
<link rel="stylesheet" href="https://fonts.googleapis.com/css2?family=Arimo:wght@400;700&display=swap">
<style>
  :root {
    --page: #e4e4e4;
    --card-dark: #303030;
    --brand-green: #0c9444;
    --text-light: #f4f4f6;
    --rule: #5a5a5a;
  }
  * { margin: 0; padding: 0; box-sizing: border-box; }
  html, body { width: 1200px; height: 1200px; overflow: hidden; }
  body {
    background: var(--page);
    font-family: "Arimo", Arial, sans-serif;
    position: relative;
  }
  .card {
    position: absolute;
    width: 690px;
    height: 394px;
    overflow: hidden;
  }
  .card--front { left: 266px; top: 158px; background: var(--card-dark); }
  .card--back  { left: 262px; top: 653px; background: var(--brand-green); }

  .front__stripe-white {
    position: absolute; left: 0; right: 0; top: 372px; height: 3px;
    background: var(--text-light);
  }
  .front__stripe-green {
    position: absolute; left: 0; right: 0; top: 378px; bottom: 0;
    background: var(--brand-green);
  }
  .front__divider {
    position: absolute; left: 376px; top: 75px; width: 1px; height: 215px;
    background: var(--rule);
  }

  .wordmark {
    position: absolute;
    display: flex; flex-direction: column; align-items: center;
    color: var(--text-light);
    font-weight: 700;
    text-transform: uppercase;
    line-height: 1;
  }
  .wordmark__main { letter-spacing: 2px; }
  .wordmark__sub { letter-spacing: 4px; }
  .card--front .wordmark { left: 40px; width: 300px; top: 140px; }
  .card--front .wordmark__main { font-size: 78px; }
  .card--front .wordmark__sub { font-size: 17px; margin-top: 14px; }
  .card--back .wordmark { left: 0; width: 690px; top: 135px; }
  .card--back .wordmark__main { font-size: 100px; }
  .card--back .wordmark__sub { font-size: 21px; margin-top: 18px; }

  .contact { position: absolute; left: 403px; top: 90px; color: var(--text-light); }
  .contact__name {
    font-size: 25px; font-weight: 700; color: var(--brand-green);
    letter-spacing: 0.3px; line-height: 1;
  }
  .contact__role { font-size: 15px; margin-top: 4px; }
  .contact__address { font-size: 15.5px; line-height: 21px; margin-top: 22px; }
  .contact__list { list-style: none; margin-top: 14px; }
  .contact__item {
    display: flex; align-items: center; gap: 12px;
    font-size: 15.5px; height: 20.5px;
  }
  .contact__icon { width: 14px; height: 14px; flex: none; fill: var(--brand-green); }
</style>
</head>
<body>

<section class="card card--front" aria-label="Card front">
  <div class="wordmark">
    <span class="wordmark__main">TMW</span>
    <span class="wordmark__sub">Home Crafting</span>
  </div>

  <div class="front__divider"></div>

  <div class="contact">
    <p class="contact__name">LIAM CARTER</p>
    <p class="contact__role">President</p>
    <p class="contact__address">412 Ridgeview Court<br>Brookfield, Canada 58213</p>
    <ul class="contact__list">
      <li class="contact__item">
        <svg class="contact__icon" viewBox="0 0 24 24" aria-hidden="true"><path d="M6.6 10.8a15.1 15.1 0 0 0 6.6 6.6l2.2-2.2c.3-.3.7-.4 1-.2 1.1.4 2.3.6 3.6.6.6 0 1 .4 1 1V20c0 .6-.4 1-1 1A17 17 0 0 1 3 4c0-.6.4-1 1-1h3.5c.6 0 1 .4 1 1 0 1.3.2 2.5.6 3.6.1.3 0 .7-.2 1z"/></svg>
        <span>555-218-4097</span>
      </li>
      <li class="contact__item">
        <svg class="contact__icon" viewBox="0 0 24 24" aria-hidden="true"><path d="M7 1h10a2 2 0 0 1 2 2v18a2 2 0 0 1-2 2H7a2 2 0 0 1-2-2V3a2 2 0 0 1 2-2zm0 3v15h10V4zm4 16.5v1h2v-1z"/></svg>
        <span>555-302-7716</span>
      </li>
      <li class="contact__item">
        <svg class="contact__icon" viewBox="0 0 24 24" aria-hidden="true"><path d="M2 5h20v14H2zm2 2v.5l8 5 8-5V7zm0 2.8V17h16V9.8l-8 5z"/></svg>
        <span>info@tmwhomecrafting.com.au</span>
      </li>
      <li class="contact__item">
        <svg class="contact__icon" viewBox="0 0 24 24" aria-hidden="true"><path d="M12 2a10 10 0 1 0 0 20 10 10 0 0 0 0-20zm-1 17.9A8 8 0 0 1 4.1 10L9 15v1a2 2 0 0 0 2 2zm6.9-2.5A2 2 0 0 0 16 16h-1v-3a1 1 0 0 0-1-1H8v-2h2a1 1 0 0 0 1-1V7h2a2 2 0 0 0 2-2v-.4a8 8 0 0 1 2.9 12.8z"/></svg>
        <span>www.tmwhomecrafting.com.au</span>
      </li>
    </ul>
  </div>

  <div class="front__stripe-white"></div>
  <div class="front__stripe-green"></div>
</section>

<section class="card card--back" aria-label="Card back">
  <div class="wordmark">
    <span class="wordmark__main">TMW</span>
    <span class="wordmark__sub">Home Crafting</span>
  </div>
</section>

</body>
</html>
```